Social Media Graphics - Oakline Push REVISED

Create 6-7 individual social media graphics (square size) to encourage folks to join our online course called:

The Harvest Ledger Circle
How to Launch a Multi-Million Business From Scratch
Sign Up Today!

IMPORTANT: Make the largest and most prominent text on the graphic be: How to Launch a Multi-Million Business From Scratch

For the color scheme of the graphics, let's try a blue color palette; make sure the graphics appeal to both men and women

Make sure each graphic contains 1 of the 3 pics attached (crop pic as needed); and make sure one of the graphics is all TEXT only.

Target Market(s)

men and women looking to start a business

Industry/Entity Type

Entrepreneurship

Colors
0054AA
0677BA
7BADD7
CADEEF
E8F1F8

Requirements
Must have
• All the text and use the 3 pics provided; one graphic can be all text; Simple, modern design that's easy to read

```html
<!DOCTYPE html>
<html lang="en">
<head>
<meta charset="utf-8">
<title>The Harvest Ledger Circle – Social Graphics</title>
<link href="https://fonts.googleapis.com/css2?family=Bebas+Neue&family=Anton&family=Poppins:wght@600;700;800&display=swap" rel="stylesheet">
<style>
:root{
  --navy:#1b2438;
  --blue-deep:#0054aa;
  --blue:#0677ba;
  --blue-bright:#0a8fd8;
  --blue-mid:#7badd7;
  --blue-pale:#cadeef;
  --blue-mist:#e8f1f8;
  --white:#ffffff;
}
*{margin:0;padding:0;box-sizing:border-box}
html,body{width:1200px;height:817px;overflow:hidden;background:var(--white)}
.board{position:relative;width:1200px;height:817px}
.post{position:absolute;width:352px;height:352px;overflow:hidden}
.post > *{position:absolute;white-space:nowrap}
.center{left:0;right:0;text-align:center}
.bebas{font-family:"Bebas Neue",Impact,sans-serif;line-height:1}
.anton{font-family:"Anton",Impact,sans-serif;line-height:1}
.pop{font-family:"Poppins",Arial,sans-serif;font-weight:800;line-height:1}
.photo{border-radius:0}

/* Post 1 */
.post-1{left:40px;top:47px;background:linear-gradient(160deg,#4fb6ea 0%,var(--blue-bright) 35%,var(--blue) 70%,var(--blue-deep) 100%)}
.post-1 .series{top:12px;font-size:22px;color:var(--white);font-family:"Poppins",sans-serif;font-weight:700}
.post-1 .photo{left:80px;top:40px;width:200px;height:200px;background:radial-gradient(ellipse at 50% 45%,#2b3a5a 0%,#1a2a4a 50%,rgba(10,60,120,0) 75%)}
.post-1 .headline{top:196px;font-size:52px;color:var(--white)}
.post-1 .subline{top:249px;font-size:31px;color:var(--white)}
.post-1 .band{left:0;top:285px;width:352px;height:36px;background:var(--navy)}
.post-1 .scratch{top:288px;font-size:33px;color:var(--white)}
.post-1 .foot{left:0;top:321px;width:352px;height:31px;background:#0a5fa0}
.post-1 .cta{top:329px;font-size:14px;color:var(--white);font-weight:700}

/* Post 2 */
.post-2{left:426px;top:47px;background:radial-gradient(circle at 50% 50%,var(--white) 0%,var(--blue-mist) 55%,var(--blue-pale) 100%)}
.post-2 .frame{left:17px;top:24px;width:318px;height:297px;border:1px dashed var(--blue);white-space:normal}
.post-2 .tab{left:40px;top:0;width:264px;height:42px;background:var(--blue-deep);border-radius:0 0 18px 18px}
.post-2 .series{top:9px;font-size:26px;color:var(--white)}
.post-2 .line-a{top:64px;font-size:42px;color:var(--navy)}
.post-2 .line-b{top:112px;font-size:56px;color:var(--blue-deep);letter-spacing:-.5px}
.post-2 .line-c{top:160px;font-size:82px;color:var(--blue-deep);letter-spacing:-1px}
.post-2 .rule{left:40px;width:272px;height:1px;background:var(--blue-mid)}
.post-2 .rule.r1{top:106px}.post-2 .rule.r2{top:242px}
.post-2 .line-d{top:248px;font-size:31px;color:var(--navy)}
.post-2 .button{left:83px;top:307px;width:186px;height:29px;border-radius:15px;background:linear-gradient(90deg,var(--blue-deep),var(--blue-bright),var(--blue-deep))}
.post-2 .cta{top:314px;font-size:16px;color:var(--white);font-weight:700}

/* Post 3 */
.post-3{left:813px;top:47px;background:linear-gradient(150deg,var(--blue-deep) 0%,var(--blue) 55%,#18c0e0 100%)}
.post-3 .series{top:12px;font-size:17px;color:var(--white);letter-spacing:2px;font-family:"Poppins",sans-serif;font-weight:800}
.post-3 .pill{left:38px;top:36px;width:274px;height:28px;border-radius:14px;background:var(--navy)}
.post-3 .pill-text{top:39px;font-size:22px;color:var(--white);font-family:"Poppins",sans-serif;font-weight:800}
.post-3 .line-a{top:70px;font-size:46px;color:var(--white)}
.post-3 .line-b{top:115px;font-size:86px;color:var(--white)}
.post-3 .band{left:0;top:202px;width:200px;height:100px;background:linear-gradient(90deg,var(--navy) 70%,#1e3a78 100%)}
.post-3 .from{left:25px;top:208px;font-size:40px;color:var(--white)}
.post-3 .scratch{left:24px;top:252px;font-size:46px;color:var(--white)}
.post-3 .cta{left:23px;top:311px;font-size:20px;color:var(--white);letter-spacing:1px}
.post-3 .photo{left:168px;top:175px;width:184px;height:177px;background:linear-gradient(180deg,rgba(20,30,50,.6),#1a1a1f 55%,#d83555 100%)}

/* Post 4 */
.post-4{left:40px;top:428px;background:var(--white)}
.post-4 .topbar{left:0;top:0;width:190px;height:22px;background:linear-gradient(90deg,#1f57d6,#2f6fe6)}
.post-4 .series{left:0;top:28px;width:190px;text-align:center;font-size:20px;color:var(--blue)}
.post-4 .photo{left:0;top:51px;width:190px;height:301px;background:linear-gradient(180deg,#1e4fc4 0%,#173a8a 45%,#0d1a3a 100%)}
.post-4 .col{left:203px;width:126px;text-align:left}
.post-4 .l1{top:22px;font-size:52px;color:var(--navy)}
.post-4 .l2{top:70px;font-size:40px;color:var(--navy)}
.post-4 .l3{top:116px;font-size:62px;color:var(--blue)}
.post-4 .l4{top:178px;font-size:47px;color:var(--blue)}
.post-4 .l5{top:223px;font-size:40px;color:var(--blue)}
.post-4 .rule{left:203px;top:264px;width:126px;height:1px;background:var(--blue-pale)}
.post-4 .l6{top:270px;font-size:28px;color:var(--navy)}
.post-4 .band{left:190px;top:303px;width:162px;height:36px;background:var(--navy)}
.post-4 .cta{left:190px;top:314px;width:162px;text-align:center;font-size:12px;letter-spacing:2px;color:var(--white);font-family:"Poppins",sans-serif;font-weight:600}

/* Post 5 */
.post-5{left:427px;top:428px;background:linear-gradient(180deg,var(--blue-pale) 0%,var(--white) 40%,var(--blue-mist) 100%)}
.post-5 .series{top:33px;font-size:15px;letter-spacing:4px;color:var(--navy);font-family:"Poppins",sans-serif;font-weight:700}
.post-5 .line-a{top:59px;font-size:25px;color:var(--navy)}
.post-5 .multi{top:88px;font-size:96px;background:linear-gradient(90deg,var(--blue-mid),var(--blue),var(--blue-deep));-webkit-background-clip:text;background-clip:text;color:transparent;letter-spacing:1px}
.post-5 .band{left:0;top:243px;width:352px;height:109px;background:linear-gradient(180deg,var(--blue-deep),var(--blue))}
.post-5 .million{top:176px;font-size:72px;color:var(--blue-deep);letter-spacing:1px}
.post-5 .line-c{top:258px;font-size:38px;color:var(--white)}
.post-5 .button{left:96px;top:307px;width:160px;height:26px;border-radius:13px;background:var(--navy)}
.post-5 .cta{top:313px;font-size:15px;color:var(--white)}

/* Post 6 */
.post-6{left:816px;top:428px;background:linear-gradient(170deg,var(--blue) 0%,var(--blue-bright) 45%,#0cb8d8 100%)}
.post-6 .tab{left:58px;top:0;width:236px;height:30px;background:var(--white);border-radius:0 0 16px 16px}
.post-6 .series{top:8px;font-size:18px;letter-spacing:1.5px;color:var(--navy)}
.post-6 .line-a{top:35px;font-size:56px;color:var(--white)}
.post-6 .line-b{top:86px;font-size:33px;color:var(--white)}
.post-6 .line-c{top:120px;font-size:56px;color:var(--white)}
.post-6 .photo{left:60px;top:178px;width:240px;height:138px;background:radial-gradient(ellipse at 50% 70%,#1a2438 0%,#1a3a6a 55%,rgba(10,140,200,0) 80%)}
.post-6 .band{left:0;top:316px;width:352px;height:36px;background:var(--navy);border-top:2px solid var(--blue-bright)}
.post-6 .cta{top:326px;font-size:15px;color:var(--white);font-weight:700}
</style>
</head>
<body>
<main class="board">

  <section class="post post-1">
    <div class="series center">THE HARVEST LEDGER CIRCLE</div>
    <div class="photo" role="img" aria-label="Two smiling course hosts, a man in a black turtleneck and a woman in a denim jacket"></div>
    <div class="headline bebas center">HOW TO LAUNCH</div>
    <div class="subline bebas center">A MULTI-MILLION BUSINESS</div>
    <div class="band"></div>
    <div class="scratch pop center">FROM SCRATCH</div>
    <div class="foot"></div>
    <div class="cta pop center">SIGN UP TODAY!</div>
  </section>

  <section class="post post-2">
    <div class="frame"></div>
    <div class="tab"></div>
    <div class="series bebas center">THE HARVEST LEDGER CIRCLE</div>
    <div class="line-a bebas center">HOW TO LAUNCH A</div>
    <div class="rule r1"></div>
    <div class="line-b anton center">MULTI-MILLION</div>
    <div class="line-c anton center">BUSINESS</div>
    <div class="rule r2"></div>
    <div class="line-d pop center">FROM SCRATCH</div>
    <div class="button"></div>
    <div class="cta pop center">SIGN UP TODAY!</div>
  </section>

  <section class="post post-3">
    <div class="series center">THE HARVEST LEDGER</div>
    <div class="pill"></div>
    <div class="pill-text center">HOW TO LAUNCH</div>
    <div class="line-a anton center">A MULTI-MILLION</div>
    <div class="line-b anton center">BUSINESS</div>
    <div class="band"></div>
    <div class="from pop">FROM</div>
    <div class="scratch anton">SCRATCH</div>
    <div class="cta bebas">SIGN UP TODAY!</div>
    <div class="photo" role="img" aria-label="Two smiling course hosts, a man in a black tee and a woman in a pink dress"></div>
  </section>

  <section class="post post-4">
    <div class="topbar"></div>
    <div class="series bebas">THE HARVEST LEDGER CIRCLE</div>
    <div class="photo" role="img" aria-label="Course hosts speaking on stage under blue lighting"></div>
    <div class="col l1 bebas">HOW TO</div>
    <div class="col l2 bebas">LAUNCH A</div>
    <div class="col l3 bebas">MULTI</div>
    <div class="col l4 bebas">MILLION</div>
    <div class="col l5 bebas">BUSINESS</div>
    <div class="rule"></div>
    <div class="col l6 bebas">FROM SCRATCH</div>
    <div class="band"></div>
    <div class="cta">SIGN UP TODAY!</div>
  </section>

  <section class="post post-5">
    <div class="series center">THE HARVEST LEDGER</div>
    <div class="line-a pop center">HOW TO LAUNCH A</div>
    <div class="multi anton center">MULTI</div>
    <div class="band"></div>
    <div class="million anton center">MILLION</div>
    <div class="line-c bebas center">BUSINESS FROM SCRATCH</div>
    <div class="button"></div>
    <div class="cta pop center">SIGN UP TODAY!</div>
  </section>

  <section class="post post-6">
    <div class="tab"></div>
    <div class="series bebas center">THE HARVEST LEDGER CIRCLE</div>
    <div class="line-a bebas center">HOW TO LAUNCH</div>
    <div class="line-b bebas center">A MULTI-MILLION BUSINESS</div>
    <div class="line-c bebas center">FROM SCRATCH</div>
    <div class="photo" role="img" aria-label="Two smiling course hosts, a man in a black turtleneck and a woman in a denim jacket"></div>
    <div class="band"></div>
    <div class="cta pop center">SIGN UP TODAY!</div>
  </section>

</main>
</body>
</html>
```